Fresh Dwelling Tract Guide needs a new Landing Page

I like to get a landing page or website with 2-3 pages to help target home buyers who are looking to buy homes from builders such as TW Residences, Morvik, P.L. Fennick, etc. The landing page/website to be non-cluttered and be able to explain to home buyers that there are many benefits to include me as their buyer's agent when they buy a brand new home from any builders.
I may want to incorporate a short explanation video (animated) on the landing page and then for the viewer to click on a button that will take them to another page where they can search for new homes from different builders.
Target Market(s)
Home buyers looking to buy brand new home from builders such as TW Residences, Morvik, P.L. Fennick, etc.
Industry/Entity Type
Real Estate
Number of Pages Required
2 page
Font styles to use
Requirements
Must have
- The landing page may have the explanation video at the bottom of the landing page (scrolled down) or there may be a CALL TO ACTION button that takes the viewer to the 2nd page to watch the explanation video. Once they watched the explanation video and are still interested, they can click on another CALL TO ACTION button that will take them to another website that they will be able to search for all the available new homes and register their contact information.
Should not have
- No clutters and no dark colors.

```html
<!DOCTYPE html>
<html lang="en">
<head>
<meta charset="utf-8">
<title>Hometown Lot Walk — Search For New Homes</title>
<link rel="stylesheet" href="https://fonts.googleapis.com/css2?family=Oswald:wght@400&family=Open+Sans:wght@400;600&family=Roboto:wght@500&display=swap">
<style>
  :root {
    --ink: #111111;
    --brown: #4e3d22;
    --olive: #a6bd3c;
    --white: #ffffff;
    --panel: rgba(255, 255, 255, 0.78);
    --footer: rgba(10, 12, 10, 0.82);
    --dot-line: rgba(255, 255, 255, 0.8);
  }
  * { margin: 0; padding: 0; box-sizing: border-box; }
  html, body { width: 1200px; height: 724px; overflow: hidden; }
  body { font-family: "Open Sans", sans-serif; color: var(--ink); }
  a { text-decoration: none; color: inherit; }

  .page { position: relative; width: 1200px; height: 724px; overflow: hidden; }

  .hero-photo {
    position: absolute; inset: 0;
    background: linear-gradient(180deg, #dfe2e6 0%, #b9c0cb 18%, #6c7a92 38%, #5f6d84 58%, #7fa347 72%, #5f8c2f 88%, #4d7426 100%);
  }

  .brand {
    position: absolute; left: 92px; top: 34px;
    display: flex; align-items: center; gap: 10px;
  }
  .brand-mark { width: 18px; height: 18px; border-radius: 50%; background: var(--olive); }
  .brand-name { font-size: 23px; font-weight: 600; color: var(--brown); line-height: 1; }

  .top-bar {
    position: absolute; top: 40px; right: 89px;
    display: flex; align-items: center; gap: 18px;
  }
  .menu-toggle { display: block; }
  .phone { display: flex; align-items: center; gap: 6px; font-size: 21px; color: var(--ink); }

  .hero-panel {
    position: absolute; left: 497px; top: 207px; width: 617px; height: 258px;
    background: var(--panel);
    text-align: center;
  }
  .hero-title {
    font-family: "Oswald", sans-serif; font-weight: 400;
    font-size: 58px; line-height: 1; letter-spacing: -0.8px;
    margin-top: 30px; color: var(--ink);
  }
  .hero-title .accent { color: var(--brown); }
  .hero-text { font-size: 20px; line-height: 32px; margin-top: 12px; color: var(--ink); }
  .cta {
    display: inline-block; margin-top: 17px;
    width: 284px; height: 53px; line-height: 53px; border-radius: 27px;
    background: var(--olive); color: var(--white);
    font-family: "Roboto", sans-serif; font-weight: 500; font-size: 19px;
    box-shadow: 0 2px 6px rgba(0,0,0,0.15);
  }

  .slide-dots { position: absolute; left: 1144px; top: 280px; }

  .site-footer {
    position: absolute; left: 0; bottom: 0; width: 1200px; height: 77px;
    background: var(--footer);
    display: flex; align-items: center;
  }
  .copyright { margin-left: 104px; color: var(--white); font-size: 17.5px; }
  .social { margin-left: auto; margin-right: 99px; display: flex; gap: 10px; }
  .social a {
    width: 25px; height: 25px; border: 1.5px solid var(--white); border-radius: 50%;
    display: flex; align-items: center; justify-content: center;
  }
  .social .social-dot { width: 7px; height: 7px; border-radius: 50%; background: var(--white); }
</style>
</head>
<body>
<main class="page">
  <div class="hero-photo" role="img" aria-label="Smiling couple standing on the front lawn of a new blue-grey two-storey house with white trim, a stone path and flower beds"></div>

  <header>
    <a class="brand" href="#">
      <span class="brand-mark"></span>
      <span class="brand-name">Hometown Lot Walk</span>
    </a>
    <div class="top-bar">
      <svg class="menu-toggle" width="26" height="22" viewBox="0 0 26 22" aria-label="Menu">
        <rect x="0" y="0" width="26" height="4" fill="#111"/>
        <rect x="0" y="9" width="26" height="4" fill="#111"/>
        <rect x="0" y="18" width="26" height="4" fill="#111"/>
      </svg>
      <span class="phone">
        <svg width="19" height="19" viewBox="0 0 19 19" aria-hidden="true">
          <rect width="19" height="19" rx="4" fill="#a6bd3c"/>
          <path d="M6 4.5c.6 0 1.2 1.6 1.4 2.3.1.5-.8 1-.7 1.4.4 1.3 1.8 2.7 3.1 3.1.4.1.9-.8 1.4-.7.7.2 2.3.8 2.3 1.4 0 .9-1 1.9-2 1.9C8 13.9 5.1 11 5.1 7.5c0-1 .1-3 .9-3z" fill="#fff"/>
        </svg>
        : 555 014 2297
      </span>
    </div>
  </header>

  <section class="hero-panel">
    <h1 class="hero-title">SEARCH FOR <span class="accent">NEW HOMES</span></h1>
    <p class="hero-text">It is a long established fact that a reader will be distracted<br>by the readable content of a page when looking</p>
    <a class="cta" href="#">Search For New Homes</a>
  </section>

  <svg class="slide-dots" width="34" height="86" viewBox="0 0 34 86" aria-label="Slide navigation">
    <line x1="8" y1="7" x2="25" y2="26" stroke="var(--dot-line)" stroke-width="1"/>
    <circle cx="8" cy="7" r="4.5" fill="#a6bd3c"/>
    <circle cx="25" cy="26" r="4.5" fill="#fff"/>
    <circle cx="25" cy="43" r="4.5" fill="#fff"/>
    <circle cx="25" cy="61" r="4.5" fill="#fff"/>
    <circle cx="25" cy="78" r="4.5" fill="#fff"/>
  </svg>

  <footer class="site-footer">
    <p class="copyright">Copyright © 2018. All Rights Reserved</p>
    <nav class="social" aria-label="Social links">
      <a href="#" aria-label="Social profile 1"><span class="social-dot"></span></a>
      <a href="#" aria-label="Social profile 2"><span class="social-dot"></span></a>
      <a href="#" aria-label="Social profile 3"><span class="social-dot"></span></a>
      <a href="#" aria-label="Social profile 4"><span class="social-dot"></span></a>
      <a href="#" aria-label="Social profile 5"><span class="social-dot"></span></a>
      <a href="#" aria-label="Email">
        <svg width="13" height="10" viewBox="0 0 13 10" aria-hidden="true">
          <rect x="0.75" y="0.75" width="11.5" height="8.5" rx="1" fill="none" stroke="#fff" stroke-width="1.3"/>
          <path d="M1 1.2l5.5 4.3 5.5-4.3" fill="none" stroke="#fff" stroke-width="1.3"/>
        </svg>
      </a>
    </nav>
  </footer>
</main>
</body>
</html>
```